Salon and Spa Distributor Business Card

Need a business card. We are are distributor in the salon and spa industry. We identify with natural beauty. Need a card with:
Company Name: Petal Quarry"
Title: "President & CEO"
Address
Company Phone number
email
website
Tag Line:" Natural Care for Every Salon"

Industry/Entity Type

Business

Contact Information for Business Card

Name: Dov Strommen
Title: "President & CEO"
Address: 31 Harlow Ln, Bexmoor, NJ 07813
Company Phone number: 800-463-5918
email: dovstrommen@petalquarry.example
website: www.petalquarry.example

Requirements
Should not have
• No black backgrounds

```html
<!DOCTYPE html>
<html lang="en">
<head>
<meta charset="utf-8">
<title>Petal Quarry — Business Card</title>
<link href="https://fonts.googleapis.com/css2?family=Didact+Gothic&family=Montserrat:wght@700&display=swap" rel="stylesheet">
<style>
  :root{
    --stage:#e9ebe8;
    --paper:#f7f7f6;
    --green:#3f9a3a;
    --green-light:#6cbf3c;
    --green-deep:#237a35;
    --ink:#555a57;
    --white:#ffffff;
  }
  html,body{margin:0;padding:0;overflow:hidden}
  .stage{
    position:relative;width:1200px;height:974px;background:var(--stage);
    font-family:"Didact Gothic",sans-serif;overflow:hidden;
  }
  .card{
    position:absolute;width:600px;height:343px;border-radius:22px;overflow:hidden;
    box-shadow:0 10px 28px rgba(0,0,0,.14);
  }
  /* back side */
  .card--back{left:520px;top:110px;background:linear-gradient(135deg,var(--green-light) 0%,var(--green) 55%,#43a23d 100%)}
  .card--back .art{position:absolute;left:0;top:0;width:330px;height:343px}
  .back-brand{position:absolute;left:318px;top:128px;display:flex;align-items:center;gap:14px}
  .brand-dot{width:34px;height:34px;border-radius:50%;background:var(--white)}
  .back-brand .brand-name{color:var(--white);font-size:34px;letter-spacing:.5px;white-space:nowrap}
  .back-tagline{position:absolute;right:56px;bottom:52px;margin:0;color:var(--white);font-size:17px;line-height:1.35;text-align:left}
  /* front side */
  .card--front{left:80px;top:500px;background:var(--paper)}
  .card--front .art{position:absolute;left:0;top:0;width:300px;height:343px}
  .front-info{position:absolute;left:292px;top:54px;right:24px}
  .front-info .brand-name{color:var(--green);font-size:40px;line-height:1;letter-spacing:.3px;white-space:nowrap}
  .tagline{color:var(--ink);font-size:15px;margin-top:6px;white-space:nowrap}
  .person{margin-top:22px}
  .person-name{font-family:"Montserrat",sans-serif;font-weight:700;color:var(--green);font-size:19px;letter-spacing:.5px}
  .person-title{color:var(--ink);font-size:15px;margin-top:2px}
  .contact{list-style:none;margin:18px 0 0;padding:0;color:var(--ink);font-size:14px;line-height:1.5}
  .contact li{display:flex;align-items:center;gap:8px;white-space:nowrap}
  .contact svg{width:13px;height:13px;flex:none;fill:var(--green)}
  .address{color:var(--ink);font-size:14px;line-height:1.5;margin-top:4px}
</style>
</head>
<body>
<main class="stage">

  <section class="card card--back" aria-label="Card back">
    <svg class="art" viewBox="0 0 330 343" role="img" aria-label="Faint illustration of a woman's profile with flowing hair and leaves">
      <defs>
        <linearGradient id="backArt" x1="0" y1="0" x2="1" y2="1">
          <stop offset="0" stop-color="#7bc94a" stop-opacity=".55"/>
          <stop offset="1" stop-color="#2f8a36" stop-opacity=".55"/>
        </linearGradient>
      </defs>
      <path d="M0 40 C80 10 190 0 260 40 C320 80 300 170 250 230 C220 270 210 310 230 343 L0 343 Z" fill="url(#backArt)"/>
    </svg>
    <div class="back-brand">
      <span class="brand-dot" aria-hidden="true"></span>
      <span class="brand-name">Petal Quarry</span>
    </div>
    <p class="back-tagline">Natural Care<br>for Every Salon</p>
  </section>

  <section class="card card--front" aria-label="Card front">
    <svg class="art" viewBox="0 0 300 343" role="img" aria-label="Illustration of a woman's profile with flowing green hair and leaves">
      <defs>
        <linearGradient id="frontArt" x1="0" y1="0" x2="1" y2="1">
          <stop offset="0" stop-color="#7ccb3f"/>
          <stop offset=".6" stop-color="#4aa53a"/>
          <stop offset="1" stop-color="#237a35"/>
        </linearGradient>
      </defs>
      <path d="M0 0 L250 0 C300 40 290 120 250 180 C215 230 205 290 240 343 L0 343 Z" fill="url(#frontArt)"/>
    </svg>
    <div class="front-info">
      <div class="brand-name">Petal Quarry</div>
      <div class="tagline">Natural Care for Every Salon</div>
      <div class="person">
        <div class="person-name">DOV STROMMEN</div>
        <div class="person-title">President &amp; CEO</div>
      </div>
      <ul class="contact">
        <li><svg viewBox="0 0 16 16" aria-hidden="true"><path d="M3.6 1.2l2.3 3-1.4 1.6c.9 2 2.5 3.6 4.5 4.5l1.6-1.4 3 2.3-1.3 2.6C6.9 13.6 2.4 9.1 1 3.7z"/></svg>800-463-5918</li>
        <li><svg viewBox="0 0 16 16" aria-hidden="true"><path d="M1 3h14v10H1z M2 4l6 5 6-5" fill="none" stroke="#3f9a3a" stroke-width="1.6"/></svg>dovstrommen@petalquarry.example</li>
        <li><svg viewBox="0 0 16 16" aria-hidden="true"><circle cx="8" cy="8" r="6.5" fill="none" stroke="#3f9a3a" stroke-width="1.4"/><path d="M1.5 8h13M8 1.5c-3 3.5-3 9.5 0 13M8 1.5c3 3.5 3 9.5 0 13" fill="none" stroke="#3f9a3a" stroke-width="1.2"/></svg>www.petalquarry.example</li>
      </ul>
      <div class="address">31 Harlow Ln<br>Bexmoor, NJ 07813</div>
    </div>
  </section>

</main>
</body>
</html>
```